Business Card for Professional Photographer

I'm looking for an eye catching modern clean design that compliments my logo/ website fonts & colours.
I specialise in architecture, corporate & commercial photography so I'm marketing to professional clients rather than portrait / wedding clients.

I would prefer to not have a solid black design.

My logo brand guide is as follows :

Main front font. : Reislust
Main font colour : #fff
Slogan front font : Ubuntu Bold
Monogram front font : Venti Medium
Container colour : #fff

I need print ready files in pdf .png & .eps formats.

Included in the files below are some screen grabs as reference to font & colours etc.

```html
<!DOCTYPE html>
<html lang="en">
<head>
<meta charset="utf-8">
<title>Sharp Angle – Business Card</title>
<link href="https://fonts.googleapis.com/css2?family=Montserrat:wght@300;400&family=Ubuntu:wght@700&family=Roboto:wght@400&display=swap" rel="stylesheet">
<style>
  :root {
    --backdrop: #3a3a3a;
    --card: #1b1b1c;
    --gold: #c9973d;
    --silver: #b8b8b8;
    --white: #ffffff;
  }
  html, body {
    margin: 0;
    padding: 0;
    width: 799px;
    height: 1200px;
    overflow: hidden;
    background: var(--backdrop);
  }
  .canvas {
    position: relative;
    width: 799px;
    height: 1200px;
  }
  .card {
    position: absolute;
    left: 60px;
    width: 680px;
    height: 390px;
    background: var(--card);
    border-radius: 4px;
    box-shadow: 0 10px 30px rgba(0,0,0,0.45);
    overflow: hidden;
  }
  .card--front { top: 100px; }
  .card--back { top: 700px; }

  /* Front */
  .front-mark {
    position: absolute;
    top: 130px;
    left: 0;
    width: 100%;
    text-align: center;
    font-family: "Montserrat", sans-serif;
    font-weight: 300;
    font-size: 40px;
    line-height: 50px;
    letter-spacing: 8px;
    color: var(--silver);
    text-transform: uppercase;
    margin: 0;
  }
  .front-url {
    position: absolute;
    top: 290px;
    left: 0;
    width: 100%;
    text-align: center;
    font-family: "Montserrat", sans-serif;
    font-weight: 400;
    font-size: 15px;
    letter-spacing: 3px;
    color: var(--gold);
    margin: 0;
  }

  /* Back */
  .brand {
    position: absolute;
    top: 34px;
    left: 40px;
  }
  .brand__name {
    font-family: "Montserrat", sans-serif;
    font-weight: 300;
    font-size: 30px;
    letter-spacing: 7px;
    color: var(--gold);
    text-transform: uppercase;
    margin: 0;
  }
  .brand__tagline {
    font-family: "Montserrat", sans-serif;
    font-weight: 400;
    font-size: 11px;
    letter-spacing: 3.5px;
    color: var(--gold);
    margin: 4px 0 0 2px;
  }
  .person {
    position: absolute;
    top: 130px;
    left: 40px;
  }
  .person__name {
    font-family: "Ubuntu", sans-serif;
    font-weight: 700;
    font-size: 21px;
    color: var(--gold);
    margin: 0;
  }
  .person__role {
    font-family: "Roboto", sans-serif;
    font-size: 15px;
    color: var(--white);
    margin: 2px 0 0;
  }
  .contact {
    position: absolute;
    top: 210px;
    left: 40px;
    list-style: none;
    margin: 0;
    padding: 0;
    font-family: "Roboto", sans-serif;
    font-size: 15px;
    color: var(--white);
  }
  .contact__item {
    display: flex;
    align-items: center;
    gap: 10px;
    height: 24px;
  }
  .contact__icon {
    width: 14px;
    height: 14px;
    fill: var(--gold);
  }
  .back-mark {
    position: absolute;
    right: 36px;
    bottom: 110px;
    font-family: "Montserrat", sans-serif;
    font-weight: 300;
    font-size: 32px;
    letter-spacing: 6px;
    color: var(--gold);
    text-transform: uppercase;
    margin: 0;
  }
</style>
</head>
<body>
<main class="canvas">

  <section class="card card--front">
    <p class="front-mark">Sharp Angle</p>
    <p class="front-url">www.sharpanglestudio.com.au</p>
  </section>

  <section class="card card--back">
    <header class="brand">
      <h1 class="brand__name">Sharp Angle</h1>
      <p class="brand__tagline">Architecture Corporate Commercial</p>
    </header>

    <div class="person">
      <h2 class="person__name">Owen Harper</h2>
      <p class="person__role">Photographer</p>
    </div>

    <ul class="contact">
      <li class="contact__item">
        <svg class="contact__icon" viewBox="0 0 24 24" aria-hidden="true"><path d="M6.6 10.8a15.1 15.1 0 0 0 6.6 6.6l2.2-2.2a1 1 0 0 1 1-.25 11.4 11.4 0 0 0 3.6.57 1 1 0 0 1 1 1V20a1 1 0 0 1-1 1A17 17 0 0 1 3 4a1 1 0 0 1 1-1h3.5a1 1 0 0 1 1 1c0 1.25.2 2.45.57 3.57a1 1 0 0 1-.25 1z"/></svg>
        <span>0412345678</span>
      </li>
      <li class="contact__item">
        <svg class="contact__icon" viewBox="0 0 24 24" aria-hidden="true"><path d="M2 5h20v14H2z M4 7v.5l8 5 8-5V7l-8 5z" fill-rule="evenodd"/></svg>
        <span>info@sharpanglestudio.com.au</span>
      </li>
      <li class="contact__item">
        <svg class="contact__icon" viewBox="0 0 24 24" aria-hidden="true"><path d="M12 2a10 10 0 1 0 0 20 10 10 0 0 0 0-20zm6.9 6h-3a15.7 15.7 0 0 0-1.4-3.6A8 8 0 0 1 18.9 8zM12 4c.8 1.2 1.5 2.5 1.9 4h-3.8c.4-1.5 1.1-2.8 1.9-4zM4.3 14a8 8 0 0 1 0-4h3.4a16 16 0 0 0 0 4zm.8 2h3a15.7 15.7 0 0 0 1.4 3.6A8 8 0 0 1 5.1 16zm3-8h-3a8 8 0 0 1 4.4-3.6A15.7 15.7 0 0 0 8.1 8zM12 20c-.8-1.2-1.5-2.5-1.9-4h3.8c-.4 1.5-1.1 2.8-1.9 4zm2.3-6H9.7a14.6 14.6 0 0 1 0-4h4.6a14.6 14.6 0 0 1 0 4zm.2 5.6a15.7 15.7 0 0 0 1.4-3.6h3a8 8 0 0 1-4.4 3.6zm1.8-5.6a16 16 0 0 0 0-4h3.4a8 8 0 0 1 0 4z"/></svg>
        <span>www.sharpanglestudio.com.au</span>
      </li>
      <li class="contact__item">
        <span>48 Harbour Rd Westbay Vic 3999</span>
      </li>
    </ul>

    <p class="back-mark">Sharp Angle</p>
  </section>

</main>
</body>
</html>
```